Consulting company requires a logo and business card design

I require a logo/business card design for a new company based in Sexsmith Alberta called TallMarsh Integrity Consulting Ltd. I plan to provide the following services: Construction management/inspection for the oil and gas industry, as well as general consulting for Asset Management, fleet management, etc. Have attached a copy of resume for use as guide for

Target Market(s)

Businesses within the oil and gas production, construction and shipping industry

Industry/Entity Type

Oil And Gas

Contact Information for Business Card

Believe should highlight, services offered, safety, quality,

Logo Text

TallMarsh Integrity Consulting (TMIC) ?

Font styles to use
Script

Requirements
Must have
• Open to all options

```html
<!DOCTYPE html>
<html lang="en">
<head>
<meta charset="utf-8">
<title>TallMarsh Integrity Consulting Ltd – Business Card</title>
<link href="https://fonts.googleapis.com/css2?family=Lato:wght@400;700&display=swap" rel="stylesheet">
<style>
  :root {
    --backdrop: #2e3033;
    --brand-red: #c8193f;
    --brand-red-deep: #b8163a;
    --ink-grey: #555a60;
    --ink-dark: #333333;
    --paper: #ffffff;
    --rule: #c9c9c9;
  }
  * { box-sizing: border-box; margin: 0; padding: 0; }
  html, body {
    width: 1200px; height: 864px; overflow: hidden;
    background: var(--backdrop);
    font-family: "Lato", sans-serif;
  }
  .stage {
    width: 1200px; height: 864px;
    display: flex; align-items: center; justify-content: center; gap: 40px;
  }
  .card {
    width: 540px; height: 309px;
    position: relative;
    border-radius: 4px;
    box-shadow: 0 12px 30px rgba(0,0,0,.35);
    overflow: hidden;
  }

  /* Back of card */
  .card--back { background: var(--brand-red); }
  .card--back .decor-circle {
    position: absolute; left: -20px; top: -60px;
    width: 300px; height: 300px; border-radius: 50%;
    background: var(--brand-red-deep);
  }
  .card--back .wordmark {
    position: absolute; right: 44px; bottom: 40px;
    color: var(--paper); text-align: left;
  }
  .wordmark__name { font-size: 30px; font-weight: 400; line-height: 1.1; }
  .wordmark__suffix { font-size: 22px; letter-spacing: 9px; line-height: 1.2; }

  /* Front of card */
  .card--front { background: var(--paper); }
  .card--front .brand {
    position: absolute; right: 30px; top: 30px;
    display: flex; align-items: flex-start; gap: 12px;
  }
  .brand__dot {
    width: 36px; height: 36px; border-radius: 50%;
    background: var(--brand-red); margin-top: 2px;
  }
  .brand__name { color: var(--brand-red); font-size: 28px; line-height: 1.1; }
  .brand__suffix { color: var(--ink-grey); font-size: 21px; letter-spacing: 8px; line-height: 1.25; }

  .person { position: absolute; left: 30px; top: 128px; }
  .person__name { color: var(--brand-red); font-size: 20px; font-weight: 700; line-height: 1.1; }
  .person__title { color: var(--ink-dark); font-size: 13px; }

  .rule {
    position: absolute; left: 150px; right: 30px; top: 150px;
    height: 1px; background: var(--rule);
  }

  .contacts {
    position: absolute; right: 30px; top: 178px;
    list-style: none; text-align: right;
  }
  .contacts li {
    display: flex; justify-content: flex-end; align-items: center; gap: 10px;
    color: var(--ink-dark); font-size: 14.5px; line-height: 23px;
  }
  .contacts svg { width: 12px; height: 12px; fill: var(--brand-red); }
</style>
</head>
<body>
<main class="stage">

  <section class="card card--back" aria-label="Business card back">
    <div class="decor-circle"></div>
    <div class="wordmark">
      <div class="wordmark__name">TallMarsh Integrity</div>
      <div class="wordmark__suffix">Consulting Ltd</div>
    </div>
  </section>

  <section class="card card--front" aria-label="Business card front">
    <div class="brand">
      <div class="brand__dot"></div>
      <div>
        <div class="brand__name">TallMarsh Integrity</div>
        <div class="brand__suffix">Consulting Ltd</div>
      </div>
    </div>

    <div class="person">
      <div class="person__name">Daniel Brooke</div>
      <div class="person__title">Managing Director</div>
    </div>

    <div class="rule"></div>

    <ul class="contacts">
      <li>044-318-2260
        <svg viewBox="0 0 24 24" aria-hidden="true"><path d="M6.6 10.8a15 15 0 0 0 6.6 6.6l2.2-2.2a1 1 0 0 1 1-.25 11.4 11.4 0 0 0 3.6.6 1 1 0 0 1 1 1V20a1 1 0 0 1-1 1A17 17 0 0 1 3 4a1 1 0 0 1 1-1h3.5a1 1 0 0 1 1 1c0 1.25.2 2.45.6 3.6a1 1 0 0 1-.25 1z"/></svg>
      </li>
      <li>123-604-5517
        <svg viewBox="0 0 24 24" aria-hidden="true"><path d="M6 2h9v5H6zM3 8h18v12H3zm4 3v2h4v-2zm0 4v2h4v-2zm7-4v2h4v-2zm0 4v2h4v-2z"/></svg>
      </li>
      <li>123-604-5517
        <svg viewBox="0 0 24 24" aria-hidden="true"><path d="M7 1h10a2 2 0 0 1 2 2v18a2 2 0 0 1-2 2H7a2 2 0 0 1-2-2V3a2 2 0 0 1 2-2zm0 3v14h10V4zm5 15.5a1 1 0 1 0 0 2 1 1 0 0 0 0-2z"/></svg>
      </li>
      <li>info@tallmarshic.com
        <svg viewBox="0 0 24 24" aria-hidden="true"><path d="M2 5h20v14H2zm2 2v.5l8 5 8-5V7z"/></svg>
      </li>
      <li>www.tallmarshic.com
        <svg viewBox="0 0 24 24" aria-hidden="true"><path d="M10.6 13.4a1 1 0 0 1 0-1.4l3.5-3.5a1 1 0 1 1 1.4 1.4L12 13.4a1 1 0 0 1-1.4 0zM8.5 19.5a4 4 0 0 1-5.6-5.6l3-3 1.4 1.4-3 3a2 2 0 0 0 2.8 2.8l3-3 1.4 1.4zm7-7-1.4-1.4 3-3a2 2 0 0 0-2.8-2.8l-3 3-1.4-1.4 3-3a4 4 0 0 1 5.6 5.6z"/></svg>
      </li>
    </ul>
  </section>

</main>
</body>
</html>
```